KTWG application splash screen

We need a 1024x768 image for use as an application splash screen.
The image will be displayed full screen on an 10 inch industrial PC 1024x768 screen while our application is launching. The image should convey that the application is "Waiting for connection to Wi-Fi access point..." and include a graphic of the industrial PC connected to the access point via an Ethernet cable. A list of troubleshooting steps should be included at the bottom of the image. The troubleshooting steps should not be the main focus of the image and should be shown in a smaller font (but still readable at 1024x768 displayed on a 10 inch screen).
I will include a mock up of the general idea of what we are looking for as well as image files for the industrial PC, a screenshot of our application to show on the PC's screen and the AP.
For general look and feel and a sense of corporate branding please review our website https://marrowgatesoilworks.example/. The splash screen should reflect corporate branding.
Target Market(s)
Users of our application
Industry/Entity Type
Agriculture
Look and feel

```html
<!DOCTYPE html>
<html lang="en">
<head>
<meta charset="utf-8">
<title>KTWG splash screen</title>
<link href="https://fonts.googleapis.com/css2?family=Archivo+Black&family=Poppins:wght@400;500;600;700&display=swap" rel="stylesheet">
<style>
  :root{
    --page:#999999;
    --black:#000000;
    --panel:#1e1e1e;
    --green:#3fbd6a;
    --white:#ffffff;
    --dash:#bdbdbd;
    --device:#2a2a2a;
    --ap:#e8e8e8;
    --signal:#d8202a;
    --icon:#3a3a3a;
  }
  *{margin:0;padding:0;box-sizing:border-box}
  html,body{width:1200px;height:1200px;overflow:hidden;background:var(--page)}
  .splash{position:absolute;left:99px;top:224px;width:1002px;height:751px;background:var(--black);overflow:hidden;font-family:'Poppins',sans-serif;color:var(--white)}
  .brand-badge{position:absolute;left:60px;top:0;width:177px;height:153px}
  .brand-name{position:absolute;left:60px;top:40px;width:177px;text-align:center;font-family:'Poppins',sans-serif;font-weight:700;font-size:38px;color:var(--black);letter-spacing:1px}
  .headline{position:absolute;left:271px;top:40px;font-family:'Archivo Black',sans-serif;font-size:42px;line-height:53px;letter-spacing:0.5px;white-space:nowrap}
  .headline .accent{color:var(--green);display:block}
  .node-label{position:absolute;font-weight:500;font-size:20px;line-height:27px}
  .node-label.cab{right:827px;top:230px;text-align:right}
  .node-label.ap{left:826px;top:230px}
  .node-label small{display:block;font-family:Arial,sans-serif;font-weight:400;font-size:12px;line-height:14px;margin-top:3px}
  .cab-computer{position:absolute;left:203px;top:203px;width:193px;height:152px;border-radius:10px;background:linear-gradient(160deg,#3a3a3a,#1a1a1a)}
  .cab-computer .screen{position:absolute;left:18px;top:16px;width:157px;height:118px;background:linear-gradient(180deg,#f2f4f2,#dfe8e1)}
  .access-point{position:absolute;left:793px;top:211px;width:16px;height:133px;border-radius:3px;background:linear-gradient(90deg,#d4d4d4,var(--ap))}
  .diagram{position:absolute;left:0;top:0}
  .cable-label{position:absolute;left:467px;top:342px;width:200px;text-align:center;font-weight:500;font-size:19px}
  .section-title{position:absolute;left:0;top:408px;width:1002px;text-align:center;font-family:'Archivo Black',sans-serif;font-size:28px;color:var(--green)}
  .section-sub{position:absolute;left:0;top:450px;width:1002px;text-align:center;font-size:14px}
  .help-panel{position:absolute;left:0;top:481px;width:1002px;height:270px;background:var(--panel)}
  .help-intro{position:absolute;left:0;top:24px;width:1002px;text-align:center;font-weight:600;font-size:18px}
  .steps{position:absolute;list-style:none;width:350px;font-size:14px;line-height:18px}
  .steps.left{left:107px;top:85px}
  .steps.right{left:608px;top:85px}
  .steps li{position:relative;margin-bottom:14px}
  .steps li::before{content:"";position:absolute;left:-18px;top:4px;width:10px;height:10px;border-radius:50%;background:var(--green)}
  .steps li::after{content:"";position:absolute;left:-15.5px;top:6.5px;width:3px;height:4px;border:solid var(--panel);border-width:0 1.5px 1.5px 0;transform:rotate(45deg)}
  .settings-icon{position:absolute;left:466px;top:87px}
</style>
</head>
<body>
<main class="splash">
  <svg class="brand-badge" viewBox="0 0 177 153"><polygon points="0,0 177,0 177,124 88.5,153 0,124" fill="#ffffff"/></svg>
  <div class="brand-name">KTWG</div>

  <h1 class="headline">WAITING FOR CONNECTION<span class="accent">TO WI-FI ACCESS POINT...</span></h1>

  <div class="node-label cab">Tractor<br>cab<br>computer</div>
  <div class="cab-computer" role="img" aria-label="Industrial tractor cab computer showing the seeding application screen"><div class="screen"></div></div>

  <svg class="diagram" width="1002" height="400" viewBox="0 0 1002 400">
    <polygon points="565,180 657,329 473,329" fill="var(--green)"/>
    <rect x="556" y="220" width="18" height="70" fill="var(--white)"/>
    <rect x="556" y="298" width="18" height="18" fill="var(--white)"/>
    <polyline points="298,360 298,378 801,378 801,350" fill="none" stroke="var(--dash)" stroke-width="3" stroke-dasharray="7 6"/>
    <g fill="none" stroke="var(--signal)" stroke-width="2" stroke-linecap="round">
      <path d="M839,232 a12,12 0 0 1 18,0"/>
      <path d="M842,236 a7,7 0 0 1 12,0"/>
    </g>
    <circle cx="848" cy="240" r="1.8" fill="var(--signal)"/>
  </svg>

  <div class="cable-label">Ethernet cable</div>
  <div class="access-point" role="img" aria-label="Outdoor Wi-Fi access point with antennas"></div>
  <div class="node-label ap">Wi-Fi<br>Access<br>Point<small>Relaynet<br>AX-200 Outdoor</small></div>

  <h2 class="section-title">Troubleshooting steps</h2>
  <p class="section-sub">This screen should only be visible for a short time on boot</p>

  <section class="help-panel">
    <p class="help-intro">If this screen stays visible for more than a</p>
    <ul class="steps left">
      <li>Verify that the Wi-Fi Access Point (AP) powers up when this system does (indicated by a green light on the side of the AP).</li>
      <li>Check the Ethernet cable between this system and the AP for damage, and replace it if necessary.</li>
    </ul>
    <svg class="settings-icon" width="106" height="106" viewBox="0 0 106 106" fill="none" stroke="var(--icon)" stroke-width="5">
      <circle cx="53" cy="53" r="38" stroke-width="14" stroke-dasharray="12 8"/>
      <circle cx="53" cy="53" r="30"/>
      <path d="M38,40 l30,30 M62,36 a10,10 0 1 0 8,14" stroke-linecap="round"/>
    </svg>
    <ul class="steps right">
      <li>Power-cycle this system and wait for it to reboot fully.</li>
      <li style="margin-top:30px">If the issue persists, contact KTWG support for further assistance.</li>
    </ul>
  </section>
</main>
</body>
</html>
```